Insurance Agency website design for Brellow Cover Insurance, LP

Build a website for Brellow Cover Insurance, LP which sells Homeowners, Auto, Renters, Condo, Flood, Disability, Life, Umbrella, and health insurance. We need the coolest insurance agency website out there to get quotes, contact us, or get additional information. Please list the following insurance companies we work with: Varnix, Ostle, Meridale Mutual, Quillor, Dunmarrow, KGZ, and Pellwick.

Make a design similar to https://www.fernagentry.com/

Selling personal insurance policies

```html
<!DOCTYPE html>
<html lang="en">
<head>
<meta charset="utf-8">
<title>Brellow Cover Insurance, LP</title>
<link href="https://fonts.googleapis.com/css2?family=Poppins:wght@600;700&family=Roboto:wght@400;500;700&display=swap" rel="stylesheet">
<style>
:root{
  --navy:#0b4a8f;
  --navy-deep:#082a54;
  --navy-footer:#0a2547;
  --blue-text:#0d4f9c;
  --teal:#1fa98a;
  --ink:#2b2b2b;
  --body:#5c5c5c;
  --pale:#dde9f6;
  --card-border:#e2e2e2;
  --white:#ffffff;
}
*{box-sizing:border-box;margin:0;padding:0}
html,body{width:1200px;height:2885px;overflow:hidden}
body{position:relative;font-family:"Roboto",sans-serif;color:var(--ink);background:var(--white)}
.abs{position:absolute}
.btn{position:absolute;display:flex;align-items:center;justify-content:center;border-radius:20px;font:700 15px "Roboto",sans-serif;color:var(--white);background:var(--teal);text-transform:uppercase}
.btn-outline{background:transparent;border:2px solid var(--white)}
/* top bar */
.topbar{left:0;top:0;width:1200px;height:38px;background:var(--navy);color:var(--white);font-size:13px;display:flex;align-items:center;justify-content:center;gap:10px}
.topbar svg{width:13px;height:13px;fill:var(--white)}
/* nav */
.nav{left:0;top:38px;width:1200px;height:99px;background:var(--white)}
.nav-links{left:143px;top:44px;display:flex;gap:30px;font:500 17px "Roboto",sans-serif;color:var(--ink)}
.nav-links .active{color:var(--teal)}
.brand{left:455px;top:25px;display:flex;align-items:center;gap:12px;color:var(--navy);font:600 24px "Poppins",sans-serif;letter-spacing:1px;text-transform:uppercase;line-height:1.1}
.brand-mark{width:34px;height:34px;background:var(--navy)}
/* hero */
.hero{left:0;top:137px;width:1200px;height:357px;background:linear-gradient(90deg,#0b4f97 0%,#0c56a3 50%,#1a62a8 100%)}
.hero-art{right:0;top:0;width:560px;height:357px;background:linear-gradient(135deg,#0f5aa5,#2670b8 60%,#1c5e9f)}
.hero h1{left:143px;top:84px;font:700 52px/60px "Poppins",sans-serif;color:var(--white)}
.band{left:0;top:494px;width:1200px;height:47px;background:#0a4585;color:var(--white);font:500 13px "Roboto",sans-serif;display:flex;align-items:center;justify-content:center;gap:26px}
/* partners */
.partner{position:absolute;font:700 30px "Poppins",sans-serif;color:#222;letter-spacing:2px;text-transform:uppercase;display:flex;align-items:center;gap:12px}
.partner i{display:inline-block;width:18px;height:18px;border-radius:50%;background:var(--blue-text)}
/* welcome */
.welcome-art{left:0;top:869px;width:560px;height:496px}
.heading{font:700 38px/46px "Poppins",sans-serif;color:var(--ink)}
.heading span{color:var(--blue-text)}
.rule{width:52px;height:3px;background:var(--teal)}
.para{font:400 14.5px/23px "Roboto",sans-serif;color:var(--body);text-align:justify}
/* cards */
.card{position:absolute;width:176px;height:171px;background:var(--white);border:2px solid var(--card-border);display:flex;flex-direction:column;align-items:center;justify-content:center;gap:22px;font:500 17px "Roboto",sans-serif;color:#222}
.card.active{background:#e9f8f4;border:3px solid #bfe9dc}
.card svg{width:70px;height:70px;fill:none;stroke:var(--blue-text);stroke-width:2.2}
.arrow-circ{position:absolute;width:45px;height:45px;border-radius:50%;border:1.5px solid #888;display:flex;align-items:center;justify-content:center}
.arrow-circ svg{width:18px;height:18px;stroke:#555;fill:none;stroke-width:2}
/* quote */
.quote{left:0;top:1943px;width:1200px;height:495px;background:var(--pale)}
.quote-photo{left:0;top:0}
.field{position:absolute;background:var(--white);border:1px solid #cfd8e3;font:400 13px "Roboto",sans-serif;color:#444;padding:16px 17px}
/* footer */
.footer{left:0;top:2438px;width:1200px;height:371px;background:var(--navy-footer);color:var(--white)}
.footer h4{position:absolute;font:700 15px "Roboto",sans-serif;text-transform:uppercase}
.footer ul{position:absolute;list-style:none;font:400 13px/27px "Roboto",sans-serif}
.contact-row{position:absolute;left:143px;display:flex;gap:20px;font:400 13px/19px "Roboto",sans-serif}
.contact-row svg{width:18px;height:18px;fill:var(--white);flex:none;margin-top:2px}
.social{position:absolute;width:30px;height:30px;border-radius:50%;border:1.5px solid var(--white)}
.copy{left:0;top:2809px;width:1200px;height:76px;background:#092040;color:var(--white);font:400 14px "Roboto",sans-serif;display:flex;align-items:center;justify-content:center}
</style>
</head>
<body>

<div class="abs topbar">
  <span>For inquiries, please contact us at</span>
  <svg viewBox="0 0 24 24"><path d="M6.6 10.8a15 15 0 0 0 6.6 6.6l2.2-2.2c.3-.3.7-.4 1-.2 1.1.4 2.3.6 3.6.6.6 0 1 .4 1 1V20c0 .6-.4 1-1 1A17 17 0 0 1 3 4c0-.6.4-1 1-1h3.5c.6 0 1 .4 1 1 0 1.3.2 2.5.6 3.6.1.3 0 .7-.2 1z"/></svg>
  <span>(555) 318-0472</span><span>&nbsp;or&nbsp;</span>
  <svg viewBox="0 0 24 24"><path d="M2 5h20v14H2z M2 5l10 8 10-8" /></svg>
  <span>info@BrellowCover.com</span>
</div>

<header class="abs nav">
  <nav class="abs nav-links"><span class="active">Home</span><span>About Us</span><span>Get a quote</span></nav>
  <div class="abs brand"><span class="brand-mark"></span><span>Brellow Cover<br>Insurance LP</span></div>
  <div class="btn" style="left:842px;top:34px;width:133px;height:39px">Contact Us</div>
  <svg class="abs" style="left:998px;top:45px;width:17px;height:17px" viewBox="0 0 24 24" fill="none" stroke="#111" stroke-width="3"><circle cx="10" cy="10" r="7"/><path d="M15 15l7 7"/></svg>
  <svg class="abs" style="left:1032px;top:47px;width:23px;height:14px" viewBox="0 0 23 14"><rect width="23" height="14" fill="#1f3f8f"/><path d="M0 0L23 14M23 0L0 14" stroke="#fff" stroke-width="3"/><path d="M11.5 0v14M0 7h23" stroke="#fff" stroke-width="4"/><path d="M11.5 0v14M0 7h23" stroke="#c8102e" stroke-width="2"/></svg>
</header>

<section class="abs hero">
  <div class="abs hero-art" role="img" aria-label="Chalk drawing of a house and rising graph being sketched by a hand on a blue board"></div>
  <h1 class="abs">Buy Insurance the<br>Smart Way</h1>
  <div class="btn" style="left:144px;top:228px;width:133px;height:40px">Contact Us</div>
  <div class="btn btn-outline" style="left:282px;top:228px;width:133px;height:40px">Get Started</div>
</section>
<div class="abs band"><span>Independent insurance agents work with these insurance companies and more. See the best insurance companies near you</span>
  <svg width="22" height="22" viewBox="0 0 22 22"><circle cx="11" cy="11" r="11" fill="#fff"/><path d="M6 11h9M11 7l4 4-4 4" stroke="#0a4585" stroke-width="2.2" fill="none"/></svg>
</div>

<section aria-label="Partner insurance companies">
  <div class="partner" style="left:144px;top:601px">Varnix</div>
  <div class="partner" style="left:396px;top:601px">Ostle</div>
  <div class="partner" style="left:568px;top:603px;font-size:24px;letter-spacing:0;text-transform:none">Meridale Mutual</div>
  <div class="partner" style="left:840px;top:601px">Dunmarrow</div>
  <div class="partner" style="left:254px;top:719px;text-transform:none;letter-spacing:0"><i></i>Quillor</div>
  <div class="partner" style="left:575px;top:719px">KGZ</div>
  <div class="partner" style="left:770px;top:719px;letter-spacing:1px"><i></i>Pellwick</div>
</section>

<section aria-label="Welcome">
  <svg class="abs welcome-art" viewBox="0 0 560 496" role="img" aria-label="Hand passing house keys over a small wooden house model">
    <defs><linearGradient id="wg" x1="0" y1="0" x2="1" y2="1"><stop offset="0" stop-color="#c9c3ba"/><stop offset=".5" stop-color="#9d8a77"/><stop offset="1" stop-color="#5e4b3c"/></linearGradient></defs>
    <polygon points="0,0 417,0 560,496 0,496" fill="url(#wg)"/>
    <polygon points="38,34 398,34 522,463 38,463" fill="none" stroke="#fff" stroke-width="2.5"/>
  </svg>
  <h2 class="abs heading" style="left:586px;top:930px">Welcome to<br><span>&nbsp;Brellow Cover Insurance</span></h2>
  <div class="abs rule" style="left:586px;top:1046px"></div>
  <p class="abs para" style="left:586px;top:1079px;width:470px">At Brellow Cover Insurance, we understand that your peace of mind is invaluable. Our mission is to protect what matters most to you—your home, your vehicle, your health, and your loved ones. With our comprehensive range of insurance solutions, we are dedicated to safeguarding your assets and providing you with the security you deserve.</p>
  <p class="abs" style="left:585px;top:1222px;font:500 19px 'Roboto',sans-serif;color:var(--blue-text)">For inquiries, please contact us at</p>
  <svg class="abs" style="left:585px;top:1269px" width="26" height="26" viewBox="0 0 26 26"><circle cx="13" cy="13" r="13" fill="var(--navy)"/><path d="M9 8l3 3-1.5 1.5a7 7 0 0 0 3 3L15 14l3 3-2 2c-4 0-9-5-9-9z" fill="#fff"/></svg>
  <span class="abs" style="left:620px;top:1271px;font:500 17px 'Roboto',sans-serif">(555) 318-0472</span>
  <svg class="abs" style="left:758px;top:1269px" width="26" height="26" viewBox="0 0 26 26"><circle cx="13" cy="13" r="13" fill="var(--teal)"/><rect x="8" y="9" width="10" height="8" fill="#fff"/></svg>
  <span class="abs" style="left:798px;top:1271px;font:500 17px 'Roboto',sans-serif">info@BrellowCover.com</span>
</section>

<section aria-label="Types of insurances">
  <h2 class="abs heading" style="left:0;width:1200px;text-align:center;top:1443px">Types of <span>Insurances</span></h2>
  <div class="abs rule" style="left:574px;top:1510px"></div>
  <div class="arrow-circ" style="left:68px;top:1645px"><svg viewBox="0 0 18 18"><path d="M12 2L5 9l7 7"/></svg></div>
  <div class="arrow-circ" style="left:1087px;top:1645px"><svg viewBox="0 0 18 18"><path d="M6 2l7 7-7 7"/></svg></div>
  <div class="card" style="left:143px;top:1558px"><svg viewBox="0 0 70 70"><path d="M6 42v-8l8-4 8-12h26l8 12 8 3v9z"/><path d="M24 21h22l5 9H19z"/><circle cx="20" cy="44" r="6"/><circle cx="50" cy="44" r="6"/></svg>AUTO</div>
  <div class="card" style="left:328px;top:1607px"><svg viewBox="0 0 70 70"><path d="M8 32L35 8l27 24M14 27v36h42V27"/><rect x="24" y="36" width="22" height="18"/><path d="M35 36v18M24 45h22"/></svg>HOMEOWNERS</div>
  <div class="card active" style="left:513px;top:1558px"><svg viewBox="0 0 70 70"><circle cx="40" cy="14" r="7"/><path d="M40 21v18M40 30h5M40 35h4"/><path d="M6 52l10-10h14l10 6-16 2M6 60l10 4 30-10 16-12"/></svg>RENTERS</div>
  <div class="card" style="left:695px;top:1607px"><svg viewBox="0 0 70 70"><rect x="20" y="6" width="30" height="58"/><path d="M6 64V26h14M64 64V26H50"/><path d="M26 14h6M38 14h6M26 24h6M38 24h6M26 34h6M38 34h6M26 44h6M38 44h6M30 64v-10h10v10M10 34h6M10 44h6M54 34h6M54 44h6"/></svg>CONDO</div>
  <div class="card" style="left:879px;top:1558px"><svg viewBox="0 0 70 70"><path d="M8 18a8 6 0 0 1 16 0 6 5 0 0 1 0 8H10a6 5 0 0 1-2-8z"/><path d="M12 32l-2 5M18 32l-2 5M24 30l-2 5"/><path d="M30 40l16-16 16 16M34 36v18h24V36"/><rect x="40" y="40" width="10" height="9"/><path d="M6 58q6-4 12 0t12 0 12 0 12 0 12 0M6 64q6-4 12 0t12 0 12 0 12 0 12 0"/></svg>FLOOD</div>
  <div class="btn" style="left:534px;top:1818px;width:133px;height:40px">View More</div>
</section>

<section class="abs quote" aria-label="Get a quote">
  <svg class="abs quote-photo" width="712" height="495" viewBox="0 0 712 495" role="img" aria-label="Insurance agent meeting with a senior client, tinted blue">
    <defs><linearGradient id="qg" x1="0" y1="0" x2="1" y2="1"><stop offset="0" stop-color="#0d4c95"/><stop offset=".6" stop-color="#0f5aa8"/><stop offset="1" stop-color="#1a5e9e"/></linearGradient></defs>
    <polygon points="0,0 711,0 569,495 0,495" fill="url(#qg)"/>
  </svg>
  <h2 class="abs" style="left:144px;top:64px;font:700 37px 'Poppins',sans-serif;color:#fff">Get A Quote</h2>
  <div class="abs rule" style="left:144px;top:134px"></div>
  <p class="abs para" style="left:144px;top:162px;width:409px;color:#fff">Brellow Cover Insurance is a full-service, independent insurance agency with over three decades of experience in delivering comprehensive insurance solutions to individuals.We proudly offer a diverse portfolio of products from more than 20 of the most reputable and financially secure companies in the industry. Our dedicated team of over 50 skilled professionals is committed to customizing these products and services to meet the unique needs of each client.</p>
  <div class="btn" style="left:144px;top:389px;width:133px;height:40px">Read More</div>
  <div class="field" style="left:731px;top:163px;width:159px;height:47px">Full Name</div>
  <div class="field" style="left:898px;top:163px;width:158px;height:47px">Phone</div>
  <div class="field" style="left:731px;top:227px;width:159px;height:47px">Email</div>
  <div class="field" style="left:898px;top:227px;width:158px;height:47px">Company</div>
  <div class="field" style="left:731px;top:291px;width:325px;height:91px">Message</div>
  <div class="btn" style="left:827px;top:398px;width:133px;height:40px">Submit</div>
</section>

<footer class="abs footer">
  <h4 style="left:144px;top:89px">Contact Us</h4>
  <div class="contact-row" style="top:140px"><svg viewBox="0 0 24 24"><path d="M12 2a7 7 0 0 0-7 7c0 5 7 13 7 13s7-8 7-13a7 7 0 0 0-7-7zm0 9.5A2.5 2.5 0 1 1 12 6.5a2.5 2.5 0 0 1 0 5z"/></svg><span>234,Excepteur sint occaecat<br>cupidatat no</span></div>
  <div class="contact-row" style="top:193px"><svg viewBox="0 0 24 24"><path d="M6.6 10.8a15 15 0 0 0 6.6 6.6l2.2-2.2c.3-.3.7-.4 1-.2 1.1.4 2.3.6 3.6.6.6 0 1 .4 1 1V20c0 .6-.4 1-1 1A17 17 0 0 1 3 4c0-.6.4-1 1-1h3.5c.6 0 1 .4 1 1 0 1.3.2 2.5.6 3.6.1.3 0 .7-.2 1z"/></svg><span>Phone:<br>(555) 318-0472</span></div>
  <div class="contact-row" style="top:244px"><svg viewBox="0 0 24 24"><path d="M2 5h20v3l-10 6L2 8zM2 10l10 6 10-6v9H2z"/></svg><span>Email:<br>info@BrellowCover.com</span></div>
  <h4 style="left:424px;top:88px">Sign up for newsletter</h4>
  <div class="abs" style="left:425px;top:140px;width:253px;height:42px;border-radius:21px;background:#fff;color:#555;font:400 14px 'Roboto',sans-serif;padding:12px 19px">Enter email</div>
  <div class="btn" style="left:425px;top:195px;width:253px;height:42px;border-radius:21px">Subscribe</div>
  <span class="social" style="left:425px;top:260px" aria-label="Social profile"></span>
  <span class="social" style="left:464px;top:260px" aria-label="Social profile"></span>
  <span class="social" style="left:504px;top:260px" aria-label="Social profile"></span>
  <span class="social" style="left:543px;top:260px" aria-label="Social profile"></span>
  <h4 style="left:742px;top:88px">Quick Links</h4>
  <ul style="left:746px;top:131px"><li>Home</li><li>About us</li><li>Get A Quote</li><li>Contact Us</li></ul>
  <h4 style="left:917px;top:88px">Other Links</h4>
  <ul style="left:921px;top:131px"><li>Local Insurance Guides</li><li>Insurance Blog</li><li>Disaster Planning</li><li>Top Categories</li></ul>
</footer>
<div class="abs copy">© 2025 Brellow Cover Insurance LP. All Rights Reserved | Privacy Policy &nbsp;| &nbsp;Terms of Use</div>

</body>
</html>
```